Professional Single Page Website Design for Tollbrook Advisory

Tollbrook Advisory is a new business consultancy specializing in providing expert services to small businesses, primarily in the brick-and-mortar retail and food service sectors. We offer a range of services including franchise development and launch, due diligence, and construction management.

Currently, we have a basic website set up at www.tollbrookadvisory.example, but we need a professional touch to enhance its design and functionality.

Project Requirements:
- Single Page Design: For now, we need a single page design that effectively showcases who we are, our services, and contact information.
- Future Expansion: The design should be flexible and scalable for future expansion to include additional pages like specific service offerings, about us, and a dedicated contact page.
- Design Aesthetic: We are looking for a modern yet professional design that aligns with our brand identity.
- Logo: We have a logo that we like, which was also sourced from Pixel Bazaar. The logo files are attached to this project brief.

Key Sections to Include:
- Hero Section: An engaging introduction to Tollbrook Advisory with a strong visual impact.
- About Us: A brief overview of who we are and our mission.
- Team: Section for the profiles of the two principals.
- Services: A clear and concise presentation of our services, including franchise development, due diligence, and construction management.
- Contact Information: Easy-to-find contact details, including a form for inquiries.
- Call to Action: Encouraging visitors to get in touch with us for consultations or further information.

Design Considerations:
- Ensure the design is responsive and mobile-friendly.
- Include high-quality images and icons that complement our services and industry.
- We do not need development services, this is only a design project.

```html
<!DOCTYPE html>
<html lang="en">
<head>
<meta charset="utf-8">
<title>Tollbrook Advisory</title>
<link href="https://fonts.googleapis.com/css2?family=Poppins:wght@300;400;500;600;700&display=swap" rel="stylesheet">
<style>
:root{
  --green:#97c8b2;
  --green-dark:#7fb59c;
  --ink:#212b33;
  --slate:#27323b;
  --text:#4a4f55;
  --white:#ffffff;
}
*{box-sizing:border-box;margin:0;padding:0}
html,body{width:1200px;height:2977px;overflow:hidden}
body{position:relative;font-family:'Poppins',sans-serif;color:var(--text);background:var(--white)}
.abs{position:absolute}

/* header */
.site-header{position:absolute;left:0;top:0;width:1200px;height:105px;background:var(--white)}
.brand{position:absolute;left:145px;top:30px;display:flex;align-items:center;gap:12px}
.brand-dot{width:40px;height:40px;border-radius:50%;background:var(--green)}
.brand-name{font-size:21px;font-weight:600;color:var(--ink);line-height:1.1}
.nav{position:absolute;top:36px;left:0;width:100%;font-size:14.5px;color:var(--ink)}
.nav a{position:absolute;text-decoration:none;color:var(--ink)}
.nav a.active{color:var(--green)}
.call{position:absolute;left:845px;top:26px;display:flex;align-items:center;gap:14px}
.call-icon{width:40px;height:40px;display:flex;align-items:center;justify-content:center}
.call-icon span{width:30px;height:30px;background:var(--green);border-radius:6px;transform:rotate(45deg);display:flex;align-items:center;justify-content:center}
.call-icon svg{transform:rotate(-45deg)}
.call-label{font-size:13.5px;color:var(--ink);line-height:1.2}
.call-number{font-size:21px;font-weight:500;color:var(--ink);line-height:1.2}

/* hero */
.hero{position:absolute;left:0;top:105px;width:1200px;height:600px;
  background:linear-gradient(100deg,#4f7896 0%,#7f9fb5 30%,#cfdce4 48%,#5a84a6 62%,#1f4466 85%,#173654 100%)}
.hero-title{position:absolute;left:141px;top:278px;font-size:45px;font-weight:700;color:var(--white);line-height:48px}
.hero-sub{position:absolute;left:144px;top:390px;font-size:16.5px;font-weight:600;color:var(--white)}
.hero-text{position:absolute;left:144px;top:424px;width:420px;font-size:13.5px;line-height:20px;color:var(--white)}
.btn{position:absolute;display:flex;align-items:center;justify-content:center;background:var(--green);color:var(--white);font-weight:600;text-transform:uppercase;letter-spacing:.2px}
.hero-btn{left:145px;top:484px;width:131px;height:38px;border-radius:20px;font-size:13px}
.scroll-cue{position:absolute;left:580px;top:685px;width:40px;height:40px;transform:rotate(45deg);background:var(--white);border-radius:6px;box-shadow:0 0 0 5px var(--white)}
.scroll-cue i{position:absolute;inset:4px;background:var(--green);border-radius:5px}
.scroll-cue svg{position:absolute;left:10px;top:10px;transform:rotate(-45deg)}

/* about */
.section-title{font-weight:700;color:var(--ink)}
.about-title{position:absolute;left:144px;top:826px;font-size:37px}
.about-text{position:absolute;left:144px;width:436px;font-size:13.4px;line-height:20px;text-align:justify}
.mission{position:absolute;left:144px;top:1058px;font-size:20px;font-weight:600;color:var(--green)}
.tile{position:absolute;transform:rotate(45deg);border-radius:26px}
.tile.photo{border:6px solid var(--white);box-shadow:0 10px 24px rgba(0,0,0,.18)}
.tile.accent{background:var(--green);border-radius:12px}

/* team */
.team-card{position:absolute;top:1380px;width:600px;height:339px}
.team-dark{left:0;background:var(--ink)}
.team-light{left:600px;background:var(--green)}
.portrait{position:absolute;top:62px;left:86px;width:110px;height:110px;transform:rotate(45deg);border-radius:22px}
.member-name{position:absolute;left:252px;top:56px;font-size:20.5px;font-weight:600;color:var(--white)}
.member-role{position:absolute;left:252px;top:85px;font-size:16.5px;font-weight:600}
.team-dark .member-role{color:var(--green)}
.team-light .member-role{color:var(--white)}
.member-bio{position:absolute;left:253px;top:120px;width:310px;font-size:14px;line-height:20px;color:var(--white)}
.ring{position:absolute;top:240px;width:44px;height:44px;border-radius:50%;border:2px solid var(--green);display:flex;align-items:center;justify-content:center}
.team-light .ring{border-color:var(--white)}

/* services */
.services-title{position:absolute;left:0;top:1808px;width:1200px;text-align:center;font-size:39px}
.tab{position:absolute;top:1899px;height:33px;background:var(--white);border-radius:8px 8px 0 0;box-shadow:0 -3px 8px rgba(0,0,0,.06);font-size:11.5px;color:var(--ink);display:flex;align-items:center;justify-content:center}
.tab.active{background:var(--green);color:var(--white)}
.service-card{position:absolute;left:145px;top:1932px;width:910px;height:382px;background:var(--green);border-radius:36px}
.service-photo{position:absolute;left:60px;top:47px;width:326px;height:287px;border-radius:8px;background:linear-gradient(135deg,#e6ecef,#c9d4da 50%,#5b7d9c 75%,#dde4e8)}
.service-heading{position:absolute;left:425px;top:36px;font-size:25px;font-weight:600;color:var(--white)}
.service-text{position:absolute;left:425px;width:437px;font-size:13.3px;line-height:20px;color:var(--white);text-align:justify}

/* contact */
.contact{position:absolute;left:0;top:2427px;width:1200px;height:550px;background:var(--slate)}
.contact-bg{position:absolute;inset:0;background:linear-gradient(180deg,rgba(39,50,59,1) 0%,rgba(45,58,68,1) 55%,rgba(60,74,84,1) 100%)}
.contact-title{position:absolute;left:144px;top:95px;font-size:37px;font-weight:600;color:var(--white)}
.contact-icon{position:absolute;left:144px;width:67px;height:67px;border-radius:50%;background:var(--green);display:flex;align-items:center;justify-content:center}
.contact-label{position:absolute;left:228px;font-size:20px;font-weight:600;color:var(--white)}
.contact-value{position:absolute;left:228px;font-size:14.5px;line-height:24px;color:var(--white)}
.field{position:absolute;background:var(--white);border-radius:4px;font-size:13.5px;color:#8b9096;padding:14px 14px}
.submit{left:516px;top:347px;width:244px;height:44px;border-radius:4px;font-size:13px}
.copyright{position:absolute;left:0;top:503px;width:1197px;text-align:center;font-size:14px;color:var(--white)}
</style>
</head>
<body>

<header class="site-header">
  <div class="brand"><span class="brand-dot"></span><span class="brand-name">Tollbrook<br>Advisory</span></div>
  <nav class="nav">
    <a class="active" style="left:434px">Home</a>
    <a style="left:507px">About</a>
    <a style="left:580px">Team</a>
    <a style="left:652px">Services</a>
    <a style="left:741px">Contact</a>
  </nav>
  <div class="call">
    <div class="call-icon"><span><svg width="14" height="14" viewBox="0 0 24 24" fill="#fff"><path d="M6.6 10.8a15.1 15.1 0 0 0 6.6 6.6l2.2-2.2a1 1 0 0 1 1-.25 11.4 11.4 0 0 0 3.6.57 1 1 0 0 1 1 1V20a1 1 0 0 1-1 1A17 17 0 0 1 3 4a1 1 0 0 1 1-1h3.5a1 1 0 0 1 1 1 11.4 11.4 0 0 0 .57 3.6 1 1 0 0 1-.25 1z"/></svg></span></div>
    <div><div class="call-label">Call Us Today :</div><div class="call-number">+1 555 014 2290</div></div>
  </div>
</header>

<section class="hero" role="img" aria-label="Looking up at a glass office tower against a pale sky">
</section>
<h1 class="hero-title">Building Success in<br>Southern California</h1>
<p class="hero-sub">Expertise at Every Step: From Planning to Execution</p>
<p class="hero-text">At Tollbrook, we blend innovative strategies with local market expertise to guide your commercial real estate ventures.</p>
<div class="btn hero-btn">Get in touch</div>
<div class="scroll-cue"><i></i><svg width="20" height="20" viewBox="0 0 24 24" fill="none" stroke="#fff" stroke-width="2.4" stroke-linecap="round" stroke-linejoin="round"><path d="M7 7l5 5 5-5M7 12l5 5 5-5"/></svg></div>

<h2 class="section-title about-title">About Us</h2>
<p class="about-text" style="top:880px">Welcome to Tollbrook Advisory, your trusted partner in navigating the complexities of the real estate and small business markets. Founded by industry veterans Daniel Reyes and Kevin Han, we specialize in providing comprehensive services tailored to the unique needs of our clients. Whether you're a franchisee, a new restaurant owner, or a commercial real estate investor, our expertise in due diligence, construction management, and investment property evaluation ensures you make informed, strategic decisions.</p>
<h3 class="mission">Mission :</h3>
<p class="about-text" style="top:1096px">At Tollbrook Advisory, we are committed to your success. Our approach combines meticulous analysis, strategic insights, and personalized service to help you achieve your business goals. We pride ourselves on our ability to deliver results that exceed expectations, fostering long-term relationships built on trust and excellence.</p>

<div class="tile photo" role="img" aria-label="Modern dark glass office building" style="left:660px;top:834px;width:195px;height:195px;background:linear-gradient(135deg,#dfe4e8,#3a4148 55%,#8c969e)"></div>
<div class="tile accent" style="left:897px;top:847px;width:56px;height:56px"></div>
<div class="tile photo" role="img" aria-label="Glass office block with trees" style="left:888px;top:958px;width:141px;height:141px;background:linear-gradient(135deg,#cfe1f0,#6f8fa8 50%,#6b8a4e)"></div>
<div class="tile accent" style="left:674px;top:1074px;width:57px;height:57px"></div>
<div class="tile photo" role="img" aria-label="White commercial building under blue sky" style="left:756px;top:1087px;width:145px;height:145px;background:linear-gradient(135deg,#3f76b8,#e4e6e8 45%,#55524e 85%)"></div>

<section class="team-card team-dark">
  <div class="portrait" role="img" aria-label="Portrait of Daniel Reyes" style="background:linear-gradient(135deg,#c9d6df,#e8e4e6)"></div>
  <h3 class="member-name">Daniel Reyes</h3>
  <div class="member-role">Principal</div>
  <p class="member-bio">Daniel Reyes brings almost 20 years of rich experience as a real estate investor and a pivotal role at one of southern California's largest real estate management firms, where he...</p>
  <div class="ring" style="left:255px"><svg width="14" height="14" viewBox="0 0 24 24" fill="#fff"><path d="M6.6 10.8a15.1 15.1 0 0 0 6.6 6.6l2.2-2.2a1 1 0 0 1 1-.25 11.4 11.4 0 0 0 3.6.57 1 1 0 0 1 1 1V20a1 1 0 0 1-1 1A17 17 0 0 1 3 4a1 1 0 0 1 1-1h3.5a1 1 0 0 1 1 1 11.4 11.4 0 0 0 .57 3.6 1 1 0 0 1-.25 1z"/></svg></div>
  <div class="ring" style="left:312px"><svg width="14" height="14" viewBox="0 0 24 24" fill="#fff"><path d="M2 5h20v14H2z"/><path d="M2 5l10 8 10-8" stroke="#212b33" stroke-width="2" fill="none"/></svg></div>
</section>
<section class="team-card team-light">
  <div class="portrait" role="img" aria-label="Portrait of Kevin Han" style="background:linear-gradient(135deg,#8a6a52,#c79b78)"></div>
  <h3 class="member-name">Kevin Han</h3>
  <div class="member-role">Principal</div>
  <p class="member-bio">Kevin Han is a seasoned real estate expert with extensive experience in project and construction management, and a licensed real estate agent in California. Fluent in both English and Korean,...</p>
  <div class="ring" style="left:255px"><svg width="14" height="14" viewBox="0 0 24 24" fill="#fff"><path d="M6.6 10.8a15.1 15.1 0 0 0 6.6 6.6l2.2-2.2a1 1 0 0 1 1-.25 11.4 11.4 0 0 0 3.6.57 1 1 0 0 1 1 1V20a1 1 0 0 1-1 1A17 17 0 0 1 3 4a1 1 0 0 1 1-1h3.5a1 1 0 0 1 1 1 11.4 11.4 0 0 0 .57 3.6 1 1 0 0 1-.25 1z"/></svg></div>
  <div class="ring" style="left:312px"><svg width="14" height="14" viewBox="0 0 24 24" fill="#fff"><path d="M2 5h20v14H2z"/><path d="M2 5l10 8 10-8" stroke="#97c8b2" stroke-width="2" fill="none"/></svg></div>
</section>

<h2 class="section-title services-title">Tollbrook Services</h2>
<div class="tab" style="left:199px;width:154px">Franchise Development</div>
<div class="tab" style="left:362px;width:114px">Due Diligence</div>
<div class="tab active" style="left:483px;width:170px">Construction Management</div>
<div class="tab" style="left:659px;width:193px">Investment Property Evaluation</div>
<div class="tab" style="left:859px;width:149px">Market Analysis</div>
<section class="service-card">
  <div class="service-photo" role="img" aria-label="Construction team reviewing blueprints on a table"></div>
  <h3 class="service-heading">Construction Management</h3>
  <p class="service-text" style="top:81px">Our Building &amp; Construction Management Services oversee every aspect of your construction and development projects, from initial planning to final completion. We ensure projects stay on time and within budget, providing meticulous attention to detail and proactive problem-solving.</p>
  <p class="service-text" style="top:201px">Specializing in tenant improvements (TIs) and ground-up construction for small to mid-size commercial projects, we handle everything from permitting and contractor coordination to quality control and final inspections. Trust us to deliver successful projects that meet your specifications and exceed your expectations, ensuring a smooth and efficient construction process every step of the way.</p>
</section>

<section class="contact">
  <div class="contact-bg" role="img" aria-label="Faint city skyline at dusk"></div>
  <h2 class="contact-title">Contact details</h2>
  <div class="contact-icon" style="top:158px"><svg width="20" height="20" viewBox="0 0 24 24" fill="#fff"><path d="M6.6 10.8a15.1 15.1 0 0 0 6.6 6.6l2.2-2.2a1 1 0 0 1 1-.25 11.4 11.4 0 0 0 3.6.57 1 1 0 0 1 1 1V20a1 1 0 0 1-1 1A17 17 0 0 1 3 4a1 1 0 0 1 1-1h3.5a1 1 0 0 1 1 1 11.4 11.4 0 0 0 .57 3.6 1 1 0 0 1-.25 1z"/></svg></div>
  <div class="contact-label" style="top:160px">Address :</div>
  <div class="contact-value" style="top:189px">412 Harbor Point Rd, Irvine,<br>CA 92620</div>
  <div class="contact-icon" style="top:256px"><svg width="20" height="20" viewBox="0 0 24 24" fill="#fff"><path d="M2 5h20v14H2z"/><path d="M2 5l10 8 10-8" stroke="#97c8b2" stroke-width="2" fill="none"/></svg></div>
  <div class="contact-label" style="top:264px">Phone :</div>
  <div class="contact-value" style="top:293px">+1 555 014 2290</div>
  <div class="contact-icon" style="top:344px"><svg width="20" height="20" viewBox="0 0 24 24" fill="#fff"><path d="M2 5h20v14H2z"/><path d="M2 5l10 8 10-8" stroke="#97c8b2" stroke-width="2" fill="none"/></svg></div>
  <div class="contact-label" style="top:352px">Email address :</div>
  <div class="contact-value" style="top:381px">hello@tollbrookadvisory.example</div>

  <div class="field" style="left:516px;top:123px;width:244px;height:45px">Name</div>
  <div class="field" style="left:771px;top:123px;width:245px;height:45px">Phone</div>
  <div class="field" style="left:516px;top:180px;width:244px;height:45px">Email</div>
  <div class="field" style="left:771px;top:180px;width:245px;height:45px">Company</div>
  <div class="field" style="left:516px;top:236px;width:498px;height:102px">Additional Information</div>
  <div class="btn submit">Submit</div>

  <p class="copyright">© Copyrights 2024 | All Rights Reserved</p>
</section>

</body>
</html>
```